Redesign (8 documents) attached with brand guidelines - very quick/easy job!

We have 8 flyers/documents that we need put into the style of our new brand (see attached). So this is a simple rebrand exercise - complete with our brand guidelines (see attached)

I would need the designer to sign an NDA prior to taking this piece of work as I will be sharing newly branded documents with you prior to market release.

If these are done well we would as the same designer to work on a z-card designed brochure/POS

Brief:

- These are documents that customers would need to complete in order to book a particular service
- If you use images (ideally from Pelvano, so we don’t have to pay for them!)
- Icon ideas enclosed
-All the content on the brochures is required: but if you think it would 'flow better' in a different order that is fine.

Target Market(s)

Customers interested in receiving a particular service

Industry/Entity Type

Work

Font styles to use
Other font styles liked:
• Brandon (see brand guide)

Requirements
Must have
• A4
Nice to have
• New logo ideas
Should not have
• Anything out of brand guidleines

```html
<!DOCTYPE html>
<html lang="en">
<head>
<meta charset="utf-8">
<title>Verdalia – Health Objectives</title>
<link rel="stylesheet" href="https://fonts.googleapis.com/css2?family=Lato:wght@400;700;900&display=swap">
<style>
  :root {
    --teal: #1b9cc1;
    --yellow: #e4e61e;
    --frame-grey: #cacaca;
    --label-grey: #5f5f5f;
    --body-grey: #707070;
    --paper: #ffffff;
  }
  * { box-sizing: border-box; margin: 0; padding: 0; }
  html, body { width: 864px; height: 1200px; overflow: hidden; }
  body { font-family: "Lato", Arial, sans-serif; background: var(--paper); }

  .sheet { position: relative; width: 864px; height: 1200px; background: var(--paper); overflow: hidden; }

  .header-band { position: absolute; left: 0; top: 0; width: 620px; height: 210px; }

  .brand { position: absolute; left: 58px; top: 74px; display: flex; align-items: center; gap: 12px; }
  .brand-dot { width: 18px; height: 18px; border-radius: 50%; background: var(--yellow); }
  .brand-name { font-weight: 900; font-size: 44px; letter-spacing: 2px; color: var(--yellow); line-height: 1; }

  .doc-title { position: absolute; right: 70px; top: 176px; font-size: 24px; font-weight: 700; color: var(--teal); }

  .field { position: absolute; display: flex; align-items: baseline; font-size: 12px; font-weight: 700; color: var(--label-grey); }
  .field-line { flex: 1; border-bottom: 2px dotted #9a9a9a; margin-left: 4px; transform: translateY(-2px); }
  .field--nutritionist { left: 432px; top: 245px; width: 362px; }
  .field--store { left: 432px; top: 294px; width: 362px; }
  .field--date { left: 432px; top: 338px; width: 362px; }
  .field--client { left: 72px; top: 338px; width: 340px; }

  .objective-table { position: absolute; left: 69px; width: 726px; background: var(--frame-grey); border-radius: 14px; padding: 4px; }
  .objective-table--one { top: 374px; }
  .objective-table--two { top: 766px; }

  .table-head { display: grid; grid-template-columns: 254px 1fr; height: 36px; align-items: center; background: var(--teal); border-radius: 11px 11px 0 0; color: #fff; font-weight: 700; font-size: 14px; }
  .table-head span { padding-left: 16px; }

  .table-row { display: grid; grid-template-columns: 252px 1fr; gap: 3px; margin-top: 3px; height: 82px; }
  .cell { background: var(--paper); border-radius: 9px; }
  .cell--question { padding: 14px 16px; font-size: 11px; line-height: 1.4; color: var(--body-grey); display: flex; align-items: center; }

  .footer-rule { position: absolute; left: 0; right: 0; top: 1180px; height: 5px; background: var(--yellow); }
  .footer-band { position: absolute; left: 0; right: 0; top: 1188px; height: 12px; background: var(--teal); }
</style>
</head>
<body>
<main class="sheet">
  <svg class="header-band" viewBox="0 0 620 210" aria-hidden="true">
    <polygon points="0,0 620,0 438,208 0,208" fill="var(--yellow)"/>
    <polygon points="0,0 608,0 430,200 0,200" fill="var(--teal)"/>
  </svg>

  <div class="brand">
    <span class="brand-dot"></span>
    <span class="brand-name">VERDALIA</span>
  </div>

  <h1 class="doc-title">Health Objectives</h1>

  <div class="field field--nutritionist">Nutritionist’s name:<span class="field-line"></span></div>
  <div class="field field--store">Store location:<span class="field-line"></span></div>
  <div class="field field--date">Date of consultation:<span class="field-line"></span></div>
  <div class="field field--client">Client’s name:<span class="field-line"></span></div>

  <section class="objective-table objective-table--one">
    <div class="table-head"><span>Reason 1</span><span>Your comments</span></div>
    <div class="table-row"><p class="cell cell--question">Symptom, issue or condition you want to address.</p><div class="cell"></div></div>
    <div class="table-row"><p class="cell cell--question">Duration - how long have you felt like this or experienced this symptom(s)?</p><div class="cell"></div></div>
    <div class="table-row"><p class="cell cell--question">Have you seen a doctor about this for a diagnosis? Did you receive any medical treatment?</p><div class="cell"></div></div>
    <div class="table-row"><p class="cell cell--question">Is there any background or extra health or lifestyle information that relates to this situation that you want your practitioner to know about? Please give details.</p><div class="cell"></div></div>
  </section>

  <section class="objective-table objective-table--two">
    <div class="table-head"><span>Reason 2</span><span>Your comments</span></div>
    <div class="table-row"><p class="cell cell--question">Symptom, issue or condition you want to address.</p><div class="cell"></div></div>
    <div class="table-row"><p class="cell cell--question">Duration - how long have you felt like this or experienced this symptom(s)?</p><div class="cell"></div></div>
    <div class="table-row"><p class="cell cell--question">Have you seen a doctor about this for a diagnosis? Did you receive any medical treatment?</p><div class="cell"></div></div>
    <div class="table-row"><p class="cell cell--question">Is there any background or extra health or lifestyle information that relates to this situation that you want your practitioner to know about? Please give details.</p><div class="cell"></div></div>
  </section>

  <div class="footer-rule"></div>
  <div class="footer-band"></div>
</main>
</body>
</html>
```